Tech business card design

We need an amazing business card design for our new business 'Pexla' a marketing tech startup based in Sydney, Australia. We provide an online marketplace for businesses to search and buy advertising media, connect with service providers and learn more about marketing. We wish to communicate 'cool tech', reliability and professionalism and design based around our logo.

Target Market(s)

Business Owners

Contact Information for Business Card

Name
Position
Email Address
Website
Phone Number

Font styles to use
Other font styles liked:
• Avenir & Avenir Next

Colors

Designer to choose colors to be used in the design.

```html
<!DOCTYPE html>
<html lang="en">
<head>
<meta charset="utf-8">
<title>Pexla Business Card</title>
<link rel="stylesheet" href="https://fonts.googleapis.com/css2?family=Exo+2:wght@700;800&family=Lato:wght@400&display=swap">
<style>
  :root {
    --navy: #0e0e3a;
    --white: #ffffff;
    --grey-text: #555559;
    --stage: #e6e4e1;
  }
  html, body {
    margin: 0;
    padding: 0;
    width: 1200px;
    height: 900px;
    overflow: hidden;
    background: var(--stage);
  }
  .stage {
    position: relative;
    width: 1200px;
    height: 900px;
  }
  .card {
    position: absolute;
    box-shadow: 3px 4px 8px rgba(0,0,0,0.35);
  }
  .card-front {
    left: 330px; top: 90px; width: 555px; height: 343px;
    background: var(--white);
  }
  .card-back {
    left: 330px; top: 469px; width: 560px; height: 343px;
    background: var(--navy);
  }
  .wordmark {
    position: absolute;
    font-family: "Exo 2", sans-serif;
    font-weight: 800;
    line-height: 1;
    letter-spacing: 1px;
    margin: 0;
  }
  .card-front .wordmark {
    left: 33px; top: 52px;
    font-size: 98px;
    color: var(--navy);
  }
  .card-back .wordmark {
    left: 0; right: 0; top: 104px;
    text-align: center;
    font-size: 112px;
    color: var(--white);
  }
  .holder-name {
    position: absolute;
    left: 32px; top: 195px;
    font-family: "Exo 2", sans-serif;
    font-weight: 700;
    font-size: 24px;
    letter-spacing: 0.5px;
    color: var(--navy);
    margin: 0;
  }
  .holder-role {
    position: absolute;
    left: 32px; top: 219px;
    font-family: "Lato", sans-serif;
    font-size: 16px;
    color: var(--grey-text);
    margin: 0;
  }
  .rule {
    position: absolute;
    left: 172px; top: 229px;
    width: 337px; height: 2px;
    background: var(--navy);
  }
  .contact-list {
    position: absolute;
    left: 277px; top: 248px;
    list-style: none;
    margin: 0; padding: 0;
    font-family: "Lato", sans-serif;
    font-size: 16px;
    color: var(--grey-text);
  }
  .contact-list li {
    display: flex;
    align-items: center;
    height: 20.5px;
  }
  .contact-list svg {
    width: 13px; height: 13px;
    margin-right: 6px;
    fill: var(--navy);
  }
</style>
</head>
<body>
<main class="stage">
  <section class="card card-front">
    <h1 class="wordmark">pexla</h1>
    <h2 class="holder-name">MARCUS HALE</h2>
    <p class="holder-role">Managing Director</p>
    <div class="rule"></div>
    <ul class="contact-list">
      <li>
        <svg viewBox="0 0 16 16" aria-hidden="true"><path d="M1 5c0-2 3-3 7-3s7 1 7 3v1h-4V4.5H5V6H1z"/><path d="M3 8l2-2h6l2 2v6H3z"/><circle cx="8" cy="10.5" r="1.6" fill="#fff"/></svg>
        044-987 654 321
      </li>
      <li>
        <svg viewBox="0 0 16 16" aria-hidden="true"><path d="M1 3h14v10H1z"/><path d="M1.5 3.5L8 9l6.5-5.5" fill="none" stroke="#fff" stroke-width="1.3"/></svg>
        info@pexlamedia.com
      </li>
      <li>
        <svg viewBox="0 0 16 16" aria-hidden="true"><circle cx="8" cy="8" r="7"/><path d="M4 5c2 0 2 2 4 2s1 3-1 3-1 3-2 3M10 3c0 2 2 2 3 3" fill="none" stroke="#fff" stroke-width="1.2"/></svg>
        www.pexlamedia.com
      </li>
    </ul>
  </section>
  <section class="card card-back">
    <p class="wordmark">pexla</p>
  </section>
</main>
</body>
</html>
```